Business Card: RW Office Partners - Your organised problem solver

Business Name: RW Office Partners
Website: www.rwofficepartners.com.au
Email: marisol@rwofficepartners.com.au
Mobile: 61 482 907 236
Facebook: @rwofficepartners
Instrgram: @rwofficepartners

Brading Colours:
HEX
#986474
#ddccd3
#7a8498
#c9d8e4
#000000
#ffffff

Tag Line: Your organised problem solver

Link to DRAFT website:
https://deskhelpcollective.wixsite.com/rw-office-partners

About Page from the website:
My name is Marisol Wrenfield, and I would love to assist you to become more productive in your day to day and achieve your business and personal goals.
My mission is to give you time, time to work on the important tasks of your business or to be able to spend more time with your family. I will take on the tasks you don’t have time for, don’t know well or simply don’t like to do.
I have an extensive background in Administration, Tender Coordination, Document Control, WHS and Quality Management working primarily in the Construction, Mining and Corporate World.
I am passionate about being organised, having order and making things in your life (and mine) easier! I love to watch something unfold and grow into something amazing! I am known for being the go-to problem solver, the organiser of all things, producing high standards of work even under pressure. I’m also a confident communicator, and I understand that you’re busy running your business.

Target Market(s)

Small to Medium Business who require assistance in their business by a virtual assistant.

Industry/Entity Type

Virtual Assistant

Contact Information for Business Card

Mobile: 61 482 907 236

Font styles to use
Sans Serif

Colors
ffffff

Requirements
Must have
• Branding Colours as outlined.
Contact Details as outlined.
Logo as provided.
Proper contact details - mobile, facebook, instragm, website.
Simple, Elegant, very clean looking.
Should not have
• Note cute with pictures.
Not too girly as still want to market to construction companies.

```html
<!DOCTYPE html>
<html lang="en">
<head>
<meta charset="utf-8">
<title>RW Office Partners – Business Card</title>
<link rel="stylesheet" href="https://fonts.googleapis.com/css2?family=Montserrat:wght@400;600&display=swap">
<style>
  :root {
    --brand-mauve: #986474;
    --brand-blush: #ddccd3;
    --brand-slate: #7a8498;
    --brand-mist: #c9d8e4;
    --ink: #1f1f1f;
    --paper: #ffffff;
    --backdrop: #4a4a4a;
  }
  * { margin: 0; padding: 0; box-sizing: border-box; }
  html, body {
    width: 1200px;
    height: 965px;
    overflow: hidden;
  }
  body {
    position: relative;
    background: var(--backdrop);
    font-family: "Montserrat", sans-serif;
  }
  .card {
    position: absolute;
    border-radius: 24px;
    box-shadow: 0 8px 22px rgba(0, 0, 0, 0.45);
  }
  .card--front {
    left: 272px;
    top: 91px;
    width: 656px;
    height: 375px;
    background: var(--brand-mauve);
  }
  .card--back {
    left: 278px;
    top: 503px;
    width: 647px;
    height: 369px;
    background: var(--paper);
  }
  .wordmark {
    position: absolute;
    font-weight: 600;
    white-space: nowrap;
    letter-spacing: 0.5px;
  }
  .card--front .wordmark {
    left: 0;
    right: 0;
    top: 148px;
    text-align: center;
    font-size: 50px;
    line-height: 60px;
    color: var(--ink);
  }
  .card--back .wordmark {
    right: 24px;
    top: 44px;
    font-size: 34px;
    line-height: 44px;
    color: var(--brand-mauve);
  }
  .contact-list {
    position: absolute;
    left: 30px;
    top: 216px;
    list-style: none;
  }
  .contact-list li {
    display: flex;
    align-items: center;
    height: 25.6px;
    font-size: 17.5px;
    color: var(--brand-slate);
  }
  .contact-icon {
    width: 16px;
    height: 16px;
    margin-right: 6px;
    flex: none;
    fill: var(--brand-mauve);
  }
  .social-mark {
    width: 14px;
    height: 14px;
    margin: 0 7px 0 1px;
    border-radius: 2px;
    background: var(--brand-mauve);
    flex: none;
  }
</style>
</head>
<body>
  <section class="card card--front" aria-label="Card front">
    <div class="wordmark">RW Office Partners</div>
  </section>

  <section class="card card--back" aria-label="Card back">
    <div class="wordmark">RW Office Partners</div>
    <ul class="contact-list">
      <li>
        <svg class="contact-icon" viewBox="0 0 16 16" aria-hidden="true">
          <rect x="4" y="0.5" width="8" height="15" rx="1.5" fill="none" stroke="#986474" stroke-width="1.5"/>
          <rect x="6.5" y="12.5" width="3" height="1.2" rx="0.6"/>
        </svg>
        61 482 907 236
      </li>
      <li><span class="social-mark"></span>@rwofficepartners</li>
      <li><span class="social-mark"></span>@rwofficepartners</li>
      <li>
        <svg class="contact-icon" viewBox="0 0 16 16" aria-hidden="true">
          <rect x="0.5" y="3" width="15" height="10" rx="1"/>
          <path d="M1 3.5 L8 9 L15 3.5" fill="none" stroke="#ffffff" stroke-width="1.2"/>
        </svg>
        marisol@rwofficepartners.com.au
      </li>
      <li>
        <svg class="contact-icon" viewBox="0 0 16 16" aria-hidden="true">
          <circle cx="8" cy="8" r="7"/>
          <path d="M1 8 H15 M8 1 V15 M3 3.8 Q8 6.5 13 3.8 M3 12.2 Q8 9.5 13 12.2" fill="none" stroke="#ffffff" stroke-width="0.9"/>
        </svg>
        www.rwofficepartners.com.au
      </li>
    </ul>
  </section>
</body>
</html>
```